Update the A4 Specials Page for Restaurant/Cafe

Provide a MINIMALIST attractive Specials page we can print weekly for our food and drink specials to give to our guests. Final design is to be provided in WORD Document so it can be easily edited by Manager. Should be black text and MINIMALIST to minimise ink usage as we print hundreds a week. We have UPLOADED the existing page as a template for you to update. Maybe logo can stay, see what you think. Or delete it and do something else. Keep it simple. Choose a good FONT. Could be a little playful with a cocktail ICON or something. Our existing menus can be seen at www.saltmeadowcafe.com.au and they are using font Alegreya. Please note we are unable to provide any feedback to designers, however we really do appreciate your time if you are submitting a design. Thank you for your participation.

```html
<!DOCTYPE html>
<html lang="en">
<head>
<meta charset="utf-8">
<title>Weekly Specials – Salt Meadow Cafe</title>
<link rel="stylesheet" href="https://fonts.googleapis.com/css2?family=Oswald:wght@500;600&family=Rubik:wght@400;500&display=swap">
<style>
  :root {
    --ink: #2b2b2b;
    --paper: #f3f3f3;
    --backdrop: #d9d6d1;
    --art: #e2e2e2;
    --white: #ffffff;
  }
  * { margin: 0; padding: 0; box-sizing: border-box; }
  html, body { width: 1200px; height: 1106px; overflow: hidden; }
  body { background: var(--backdrop); font-family: "Rubik", sans-serif; color: var(--ink); position: relative; }

  .specials-page {
    position: absolute; left: 225px; top: 23px; width: 750px; height: 1060px;
    background: var(--paper); box-shadow: 0 4px 18px rgba(0,0,0,0.12);
  }
  .page-frame {
    position: absolute; inset: 30px; border: 2px dashed var(--ink);
  }
  .brand-band {
    position: absolute; left: 50%; transform: translateX(-50%); top: 0;
    width: 200px; height: 100px; background: var(--ink);
    display: flex; align-items: flex-end; justify-content: center; padding-bottom: 14px;
  }
  .brand-name {
    font-family: "Oswald", sans-serif; font-weight: 500; font-size: 18px;
    letter-spacing: 2px; color: var(--white); text-align: center; line-height: 1.15;
  }
  .section-title {
    position: absolute; left: 0; right: 0; text-align: center;
    font-family: "Oswald", sans-serif; font-weight: 600; font-size: 58px;
    letter-spacing: 0.5px; line-height: 1; text-transform: uppercase;
  }
  .item-label {
    position: absolute; left: 50%; transform: translateX(-50%);
    background: var(--ink); color: var(--white);
    font-family: "Rubik", sans-serif; font-weight: 500; font-size: 15px;
    letter-spacing: 1px; text-transform: uppercase;
    padding: 7px 44px; white-space: nowrap;
  }
  .item-text {
    position: absolute; left: 0; right: 0; text-align: center;
    font-size: 17px; line-height: 1.45;
  }
  .price {
    position: absolute; left: 50%; transform: translateX(-50%);
    width: 44px; height: 44px; border: 2px solid var(--ink); border-radius: 50%;
    display: flex; align-items: center; justify-content: center;
    font-family: "Oswald", sans-serif; font-weight: 500; font-size: 17px;
  }
  .beer-lines .caps { text-transform: uppercase; }
  .illustration { position: absolute; background: var(--art); border-radius: 6px; }
</style>
</head>
<body>
  <main class="specials-page">
    <div class="page-frame"></div>

    <div class="brand-band"><span class="brand-name">SALT MEADOW<br>CAFE</span></div>

    <h1 class="section-title" style="top:118px;">Weekly Specials</h1>

    <div class="item-label" style="top:190px;">Chicken Filo</div>
    <p class="item-text" style="top:232px;">Creamy Chicken with Pinenuts, wrapped in Filo Pastry.<br>Served with Side Salad &amp; Zulu Sauce</p>
    <div class="price" style="top:294px;">$24</div>

    <div class="illustration" role="img" aria-label="Line drawing of a bunch of grapes with vine leaves" style="left:60px; top:350px; width:160px; height:150px;"></div>
    <div class="illustration" role="img" aria-label="Line drawing of a wine bottle with two glasses and peaches" style="left:560px; top:290px; width:140px; height:200px;"></div>

    <div class="item-label" style="top:360px;">Minestrone Soup</div>
    <p class="item-text" style="top:402px;">Served with Garlic Bread</p>
    <div class="price" style="top:440px;">$8</div>

    <h2 class="section-title" style="top:510px;">Cocktail Special</h2>

    <div class="item-label" style="top:582px;">Passionista</div>
    <p class="item-text" style="top:622px;">Vodka, Passionfruit Pulp, Mango Puree<br>Top up with Ginger &amp; Lemon Kombucha</p>
    <div class="price" style="top:684px;">$17</div>

    <h2 class="section-title" style="top:745px;">Craft Beer Special</h2>

    <div class="illustration" role="img" aria-label="Line drawing of a cocktail glass with ice cubes, citrus slice and mint" style="left:40px; top:820px; width:190px; height:225px;"></div>
    <div class="illustration" role="img" aria-label="Line drawing of a spirits bottle and a glass with ice" style="left:540px; top:815px; width:180px; height:230px;"></div>

    <p class="item-text beer-lines" style="top:815px;">
      <span class="caps">Copper Gecko</span><br>
      <span class="caps">Sunset Crush</span><br>
      Tropical Pale Ale<br>
      4.8% Alc.
    </p>
    <div class="price" style="top:928px;">$10</div>
  </main>
</body>
</html>
```